Brightfen Business Card Redesign & Logo Update

We need to update our business cards to something more modern and fresh. Brightfen can provide the current color schemes and old design examples, but welcome creativity in helping us with this redesign. PLEASE NOTE that we no longer utilize the "tree" and/or "leaf" imagery in our branding. If able would apprecaite an update on the quality of our "words only" logo in Ai. / PNG formats too.

Target Market(s)

Investors, landowners, corporate partners, contractors

Industry/Entity Type

Environmental Restoration & Conservation

Contact Information for Business Card

Logo, persons name, title, mailing address, phone and email, website url

Font styles to use
Other font styles liked:
• Merriweather

Requirements
Nice to have
• Logo, persons name, title, mailing address, phone and email, website url, but open to ideams
Should not have
• No all back backgrounds

```html
<!DOCTYPE html>
<html lang="en">
<head>
<meta charset="utf-8">
<title>Brightfen Business Cards</title>
<link rel="stylesheet" href="https://fonts.googleapis.com/css2?family=Oswald:wght@600&family=Montserrat:wght@500;700&display=swap">
<style>
  :root {
    --green: #17803f;
    --orange: #ec7f22;
    --white: #ffffff;
    --ink: #1d1d1d;
    --backdrop: #e4e5e3;
  }
  * { margin: 0; padding: 0; box-sizing: border-box; }
  html, body { width: 1200px; height: 900px; overflow: hidden; background: var(--backdrop); }
  .canvas {
    width: 1200px; height: 900px;
    display: flex; flex-direction: column; align-items: center; justify-content: center; gap: 36px;
  }
  .card {
    position: relative; width: 700px; height: 400px; overflow: hidden;
    box-shadow: 0 10px 24px rgba(0,0,0,0.18);
  }
  .card-front { background: var(--green); display: flex; align-items: center; justify-content: center; }
  .wordmark {
    font-family: "Oswald", sans-serif; font-weight: 600; text-transform: uppercase;
    letter-spacing: 2px; line-height: 1;
  }
  .card-front .wordmark { color: var(--white); font-size: 118px; }
  .card-back { background: var(--white); }
  .band-top {
    position: absolute; left: 0; right: 0; top: 0; height: 24px;
    background: var(--green); border-bottom: 6px solid var(--orange);
  }
  .band-bottom {
    position: absolute; left: 0; right: 0; bottom: 0; height: 30px;
    background: var(--green); border-top: 6px solid var(--orange);
  }
  .card-back .wordmark {
    position: absolute; right: 52px; top: 70px; color: var(--green); font-size: 66px;
  }
  .person { position: absolute; left: 52px; top: 172px; font-family: "Montserrat", sans-serif; }
  .person-name { font-weight: 700; font-size: 22px; color: var(--green); letter-spacing: 0.5px; }
  .person-name .surname { color: var(--orange); }
  .person-title { font-weight: 500; font-size: 15px; color: var(--ink); margin-top: 3px; }
  .contacts {
    position: absolute; left: 120px; top: 252px; list-style: none;
    font-family: "Montserrat", sans-serif; font-weight: 500; font-size: 17px; color: var(--ink);
  }
  .contacts li { display: flex; align-items: center; gap: 12px; height: 28px; }
  .contacts svg { width: 20px; height: 20px; flex: none; }
  .address {
    position: absolute; right: 52px; top: 246px; text-align: right; font-style: normal;
    font-family: "Montserrat", sans-serif; font-weight: 500; font-size: 16px; line-height: 1.45; color: var(--ink);
  }
</style>
</head>
<body>
<main class="canvas">
  <section class="card card-front">
    <h1 class="wordmark">Brightfen</h1>
  </section>

  <section class="card card-back">
    <div class="band-top" aria-hidden="true"></div>
    <div class="band-bottom" aria-hidden="true"></div>

    <div class="wordmark">Brightfen</div>

    <div class="person">
      <div class="person-name">DAN <span class="surname">HOLLOWAY</span></div>
      <div class="person-title">Managing Director</div>
    </div>

    <ul class="contacts">
      <li>
        <svg viewBox="0 0 20 20"><circle cx="10" cy="10" r="10" fill="#ec7f22"/><path d="M6.5 5.5l2 2-1 1.2a6 6 0 0 0 3.8 3.8l1.2-1 2 2-1.2 1.3c-3.6-.4-7.5-4.3-7.9-7.9z" fill="#fff"/></svg>
        555-210-4417
      </li>
      <li>
        <svg viewBox="0 0 20 20"><circle cx="10" cy="10" r="10" fill="#ec7f22"/><rect x="5" y="6.5" width="10" height="7" fill="#fff"/><path d="M5 6.5l5 4 5-4" stroke="#ec7f22" stroke-width="1" fill="none"/></svg>
        info@brightfen.com
      </li>
      <li>
        <svg viewBox="0 0 20 20"><circle cx="10" cy="10" r="10" fill="#ec7f22"/><circle cx="10" cy="10" r="5" fill="none" stroke="#fff" stroke-width="1.4"/><path d="M5 10h10M10 5c-2.4 3-2.4 7 0 10M10 5c2.4 3 2.4 7 0 10" stroke="#fff" stroke-width="1" fill="none"/></svg>
        www.brightfen.com
      </li>
    </ul>

    <address class="address">
      42-07 Larch Street 5<br>Fernvale, NY 10492
    </address>
  </section>
</main>
</body>
</html>
```